Marlowby Services Website Design

We have most content but require a professional design. We have a logo already and will need it utilized along with several of the photos from the attached documentation.
First page should have our mission and Vision and the synapsis provided in the word document. Visitors will be prompted to select from one of our 3 divisions from this page.
Each division will have the same list of tabs : About, Services, Safety, Careers and Contact.
Photos on each divisions page should be representative of the divisions offerings. The word doc attached contains the requested content and we are open to edits that would complement and fill the website.
I like the Quorvane site www.quorvane.example - they are our competition so cant be modeled directly after this.
Please include prompts to request quote at each service page. align the format of the geotechnical page to the other 2 divisions.
I used chat gpt for some of the content so will need it optimized for SCO.

```html
<!DOCTYPE html>
<html lang="en">
<head>
<meta charset="utf-8">
<title>Marlowby Services</title>
<link rel="stylesheet" href="https://fonts.googleapis.com/css2?family=Krona+One&family=Oswald:wght@500;600&family=Poppins:wght@400;500;600&family=Lato:wght@400;700&display=swap">
<style>
:root{
  --red:#ee1c24;
  --red-dark:#b5121a;
  --ink:#1a1a1a;
  --text:#333333;
  --grey-bg:#f4f4f4;
  --footer:#24272c;
  --footer-deep:#1b1d21;
  --white:#ffffff;
}
*{box-sizing:border-box;margin:0;padding:0}
html,body{width:1200px;height:3318px;overflow:hidden;background:var(--white)}
.page{position:relative;width:1200px;height:3318px;overflow:hidden;font-family:"Poppins",sans-serif;color:var(--text)}
.abs{position:absolute}

/* header */
.site-header{left:0;top:0;width:1200px;height:63px;background:var(--white)}
.brand{left:140px;top:12px;font-family:"Krona One",sans-serif;font-size:31px;color:var(--red);letter-spacing:1px;line-height:40px}
.main-nav{left:640px;top:0;height:63px;display:flex;align-items:center;font-family:"Lato",sans-serif;font-size:13px;color:var(--ink)}
.main-nav a{color:inherit;text-decoration:none;margin-right:43px}
.btn{display:inline-block;background:var(--red);color:var(--white);font-family:"Lato",sans-serif;text-decoration:none;text-align:center}
.main-nav .btn{margin:0;width:118px;height:34px;line-height:34px;font-size:14px}

/* hero */
.hero{left:0;top:63px;width:1200px;height:600px;background:linear-gradient(100deg,#07111f 0%,#0d2440 30%,#1b4f80 55%,#2d6aa0 70%,#0e2238 100%)}
.hero-title{left:145px;top:183px;font-family:"Oswald",sans-serif;font-weight:600;font-size:48px;line-height:54px;color:var(--white)}
.hero-sub{left:143px;top:355px;width:450px;font-family:"Lato",sans-serif;font-size:20px;line-height:26px;color:var(--white)}
.hero .btn{left:142px;top:427px;width:116px;height:34px;line-height:34px;font-size:14px}

/* section headings */
.section-title{left:0;width:1200px;text-align:center;font-family:"Krona One",sans-serif;font-size:31px;letter-spacing:4px;color:var(--ink)}
.section-title .accent,.split-title .accent{color:var(--red)}

/* divisions */
.division{top:828px;width:286px;height:328px}
.division-label{left:0;top:236px;width:286px;text-align:center;font-size:17px;line-height:21px;font-weight:500;color:var(--white);letter-spacing:.5px}

/* services */
.services-band{left:0;top:1243px;width:1200px;height:672px;background:var(--grey-bg)}
.service-card{top:1393px;width:438px;height:318px}
.service-caption{top:1738px;width:438px;text-align:center;font-size:18px;line-height:26px;color:var(--ink)}
.service-caption b{font-weight:600}

/* vision */
.vision-text{left:142px;top:1990px}
.split-title{font-family:"Krona One",sans-serif;font-size:32px;letter-spacing:4px}
.vision-text .split-title{color:var(--white)}
.vision-text p{margin-top:18px;width:390px;font-size:15.5px;line-height:25.5px;color:var(--white)}

/* mission */
.dots{left:104px;top:2325px;width:112px;height:112px;background-image:radial-gradient(#c9c9c9 1.2px,transparent 1.4px);background-size:8px 8px}
.stat-badge{left:434px;top:2652px;width:131px;height:131px;background:var(--red);border-top:6px solid var(--white);border-left:6px solid var(--white);color:var(--white);text-align:center}
.stat-badge .num{font-family:"Oswald",sans-serif;font-weight:600;font-size:60px;line-height:72px;margin-top:4px}
.stat-badge .lbl{font-size:13px;line-height:16px;letter-spacing:1px}
.mission-text{left:618px;top:2418px;width:442px}
.mission-text .split-title{color:var(--ink)}
.mission-text p{font-size:15.5px;line-height:25.7px;color:var(--text)}
.mission-text p+p{margin-top:10px}
.mission-text .split-title+p{margin-top:22px}
.mission-text b{font-weight:600;color:var(--ink)}

/* footer */
.footer{left:0;top:2817px;width:1200px;height:501px;background:var(--footer)}
.footer-logo{left:0;top:3000px;width:1200px;text-align:center;font-family:"Krona One",sans-serif;font-size:44px;line-height:56px;color:var(--white);letter-spacing:2px}
.footer-nav{top:3091px;font-size:13px;font-weight:500;color:var(--white);letter-spacing:.5px}
.contact{top:3184px;display:flex;align-items:center;color:var(--white)}
.contact .icon{width:44px;height:44px;border:1.5px solid var(--white);border-radius:50%;display:flex;align-items:center;justify-content:center;margin-right:10px}
.contact small{display:block;font-size:13px;line-height:19px;letter-spacing:.5px}
.contact strong{display:block;font-size:20px;line-height:24px;letter-spacing:2px;font-weight:600}
.bottom-bar{left:0;top:3268px;width:1200px;height:50px;background:var(--footer-deep)}
.copyright{left:143px;top:3284px;font-size:13px;color:var(--white)}
.follow{left:876px;top:3268px;width:324px;height:50px;background:var(--red);clip-path:polygon(22px 0,100% 0,100% 100%,0 100%);display:flex;align-items:center;padding-left:44px;color:var(--white);font-size:13px;font-weight:500;letter-spacing:1px}
.follow .ring{width:32px;height:32px;border:1.5px solid var(--white);border-radius:50%;margin-left:8px}
</style>
</head>
<body>
<div class="page">

  <header class="site-header abs">
    <div class="brand abs">MARLOWBY</div>
    <nav class="main-nav abs">
      <a href="#">About</a><a href="#">Services</a><a href="#">Safety</a><a href="#">Careers</a>
      <a class="btn" href="#">Contact Us</a>
    </nav>
  </header>

  <section class="hero abs" role="img" aria-label="Night view of an illuminated industrial refinery with pipes and towers">
    <h1 class="hero-title abs">Delivering Safe,<br>Reliable Aerial Access<br>&amp; Maintenance Services</h1>
    <p class="hero-sub abs">To Oil &amp; Gas,Construction, Utility, &amp; Renewable Energy Sector</p>
    <a class="btn abs" href="#">Contact Us</a>
  </section>

  <h2 class="section-title abs" style="top:755px"><span class="accent">SELECT</span> DIVISION</h2>

  <div class="division abs" style="left:140px">
    <svg width="286" height="328" viewBox="0 0 286 328">
      <defs><linearGradient id="g1" x1="0" y1="0" x2="0" y2="1"><stop offset="0" stop-color="#9aa2a8"/><stop offset="1" stop-color="#a89377"/></linearGradient></defs>
      <polygon points="143,0 286,76 286,225 0,225 0,76" fill="url(#g1)" role="img" aria-label="White aerial boom truck parked on a dirt lot"/>
      <polygon points="0,225 286,225 286,248 143,328 0,248" fill="var(--red)"/>
      <polygon points="108,309 178,309 143,328" fill="var(--red-dark)"/>
      <path d="M137 313l5 4-5 4M144 313l5 4-5 4" stroke="#fff" stroke-width="2" fill="none"/>
    </svg>
    <div class="division-label abs">AERIAL<br>ACCESS</div>
  </div>
  <div class="division abs" style="left:457px">
    <svg width="286" height="328" viewBox="0 0 286 328">
      <defs><linearGradient id="g2" x1="0" y1="0" x2="0" y2="1"><stop offset="0" stop-color="#3f6b3a"/><stop offset=".5" stop-color="#b42a2d"/><stop offset="1" stop-color="#2b2b2b"/></linearGradient></defs>
      <polygon points="143,0 286,76 286,225 0,225 0,76" fill="url(#g2)" role="img" aria-label="Red tracked geotechnical drilling rig on grass"/>
      <polygon points="0,225 286,225 286,248 143,328 0,248" fill="var(--red)"/>
      <polygon points="108,309 178,309 143,328" fill="var(--red-dark)"/>
      <path d="M137 313l5 4-5 4M144 313l5 4-5 4" stroke="#fff" stroke-width="2" fill="none"/>
    </svg>
    <div class="division-label abs">GEOTECHNICAL<br>DRILLING</div>
  </div>
  <div class="division abs" style="left:773px">
    <svg width="286" height="328" viewBox="0 0 286 328">
      <defs><linearGradient id="g3" x1="0" y1="0" x2="1" y2="1"><stop offset="0" stop-color="#1e5fc0"/><stop offset="1" stop-color="#5a96e6"/></linearGradient></defs>
      <polygon points="143,0 286,76 286,225 0,225 0,76" fill="url(#g3)" role="img" aria-label="Aerial boom reaching toward a wind turbine against blue sky"/>
      <polygon points="0,225 286,225 286,248 143,328 0,248" fill="var(--red)"/>
      <polygon points="108,309 178,309 143,328" fill="var(--red-dark)"/>
      <path d="M137 313l5 4-5 4M144 313l5 4-5 4" stroke="#fff" stroke-width="2" fill="none"/>
    </svg>
    <div class="division-label abs">RENEWABLE ENERGY<br>SERVICES</div>
  </div>

  <div class="services-band abs"></div>
  <h2 class="section-title abs" style="top:1322px"><span class="accent">MARLOWBY</span> SERVICE</h2>

  <svg class="service-card abs" style="left:140px" viewBox="0 0 438 318">
    <polygon points="0,0 388,0 438,50 438,318 0,318" fill="#fff"/>
    <polygon points="5,5 386,5 433,52 433,313 5,313" fill="#8f9690" role="img" aria-label="Overhead view of an aerial lift truck on a residential street"/>
  </svg>
  <svg class="service-card abs" style="left:622px" viewBox="0 0 438 318">
    <polygon points="0,0 388,0 438,50 438,318 0,318" fill="#fff"/>
    <polygon points="5,5 386,5 433,52 433,313 5,313" fill="#8da3bb" role="img" aria-label="Worker in safety vest servicing a wellhead beside a rig"/>
  </svg>
  <p class="service-caption abs" style="left:124px">Delivering Safe, Reliable <b>Aerial Access</b></p>
  <p class="service-caption abs" style="left:622px"><b>Maintenance services</b> to Oil&amp;Gas, Construction, Utility, &amp; Renewable energy industries.</p>

  <svg class="abs" style="left:0;top:1872px" width="1200" height="406" viewBox="0 0 1200 406">
    <polygon points="0,43 679,43 554,356 0,356" fill="var(--red)"/>
    <polygon points="679,0 1200,0 1200,406 538,406" fill="#7f8a80" role="img" aria-label="Aerial view of a small town with a boom truck holding a sign"/>
  </svg>
  <div class="vision-text abs">
    <h2 class="split-title">OUR VISION</h2>
    <p>To be the leading provider of aerial access, geotechnical drilling, and service solutions, setting the standard for excellence in safety, efficiency, and environmental stewardship.</p>
  </div>

  <div class="dots abs"></div>
  <svg class="abs" style="left:142px;top:2364px" width="379" height="376" viewBox="0 0 379 376">
    <polygon points="0,0 314,0 379,65 379,376 0,376" fill="#6e9ad6" role="img" aria-label="Aerial boom truck parked beside a town water tower"/>
  </svg>
  <div class="stat-badge abs">
    <div class="num">65+</div>
    <div class="lbl">YEARS OF<br>EXPERIENCE</div>
  </div>
  <div class="mission-text abs">
    <h2 class="split-title"><span class="accent">OUR</span> MISSION</h2>
    <p><b>At Marlowby, our mission</b> is to deliver unparalleled aerial access, geotechnical drilling, and service and maintenance solutions, consistently exceeding our clients' expectations.</p>
    <p>We strive to achieve this by investing in cutting-edge technology, fostering a culture of safety and continuous improvement, and prioritizing environmental sustainability. Through collaboration, integrity, and dedication, we aim to contribute to the success of our clients while maintaining the highest standards of quality and professionalism.</p>
  </div>

  <footer class="footer abs" role="img" aria-label="Dim city skyline at dusk behind the footer">
    <svg class="abs" style="left:0;top:0" width="1200" height="110" viewBox="0 0 1200 110">
      <polygon points="0,0 1200,0 1200,14 600,108 0,14" fill="var(--red)"/>
      <polygon points="0,0 1200,0 600,92" fill="#fff"/>
    </svg>
  </footer>
  <div class="footer-logo abs">MARLOWBY</div>
  <div class="footer-nav abs" style="left:321px">AERIAL ACCESS</div>
  <div class="footer-nav abs" style="left:475px">GEOTECHNICAL DRILLING</div>
  <div class="footer-nav abs" style="left:689px">RENEWABLE ENERGY SERVICES</div>

  <div class="contact abs" style="left:142px">
    <div class="icon"><svg width="16" height="20" viewBox="0 0 16 20"><path d="M8 0a8 8 0 0 0-8 8c0 6 8 12 8 12s8-6 8-12a8 8 0 0 0-8-8z" fill="#fff"/><circle cx="8" cy="8" r="3" fill="var(--footer)"/></svg></div>
    <div><small>18 Ridgeway Ave.</small><small>Alder Flats, AB T0C-4K1</small></div>
  </div>
  <div class="contact abs" style="left:463px">
    <div class="icon"><svg width="20" height="20" viewBox="0 0 20 20"><path d="M4 1l4 4-2 3c1 3 3 5 6 6l3-2 4 4-3 3C9 19 1 11 1 4z" fill="#fff"/></svg></div>
    <div><small>Call Us Today!</small><strong>555.014.2270</strong></div>
  </div>
  <div class="contact abs" style="left:793px">
    <div class="icon"><svg width="18" height="14" viewBox="0 0 18 14"><rect width="18" height="14" rx="2" fill="#fff"/><path d="M1 2l8 6 8-6" stroke="var(--footer)" stroke-width="1.6" fill="none"/></svg></div>
    <div><small>Email Now!</small><small>sales@marlowbyservices.example</small></div>
  </div>

  <div class="bottom-bar abs"></div>
  <p class="copyright abs">© 2024 Marlowby Services Inc. All Rights Reserved.</p>
  <div class="follow abs">Follow Us On:<span class="ring"></span></div>

</div>
</body>
</html>
```